Business Card Design Project

We need a new fresh business card for our business. There are multiple services we offer and we need a fresh corporate card that represents us better. We start from cleaning carpet and tiles, to upholstery and curtains, to completely clean all contents and building materials after a fire, or completely dry out a home or business after a major or minor flood event. We are open to all concepts as we want to create a new look, maybe even logo, signage, vehicle signage, uniforms.
We are open to new colours etc.

Go to www.brolvaquincare.com.au for current logo and all other past ideas

Target Market(s)

Everyone is our possible client but we are targeting more coorporate

Industry/Entity Type

Building

```html
<!DOCTYPE html>
<html lang="en">
<head>
<meta charset="utf-8">
<title>Brolvaquin Care – Business Card</title>
<link rel="stylesheet" href="https://fonts.googleapis.com/css2?family=Exo+2:wght@400;500;600;700&display=swap">
<style>
  :root {
    --brand-blue: #1b5ea6;
    --brand-pink: #e0177f;
    --card-white: #ffffff;
    --card-grey: #e9eaec;
    --ink: #2d2d2d;
    --backdrop: #d9d6d2;
  }
  html, body {
    margin: 0;
    width: 1200px;
    height: 900px;
    overflow: hidden;
    background: var(--backdrop);
    font-family: "Exo 2", sans-serif;
  }
  .card {
    position: absolute;
    left: 110px;
    top: 170px;
    width: 980px;
    height: 560px;
    border-radius: 44px;
    overflow: hidden;
    background: linear-gradient(160deg, var(--card-white) 30%, var(--card-grey) 100%);
    box-shadow: 0 10px 30px rgba(0,0,0,0.18);
  }
  .card__waves {
    position: absolute;
    inset: 0;
  }
  .brand {
    position: absolute;
    left: 58px;
    top: 78px;
    display: flex;
    align-items: center;
    gap: 14px;
  }
  .brand__name {
    background: var(--brand-blue);
    color: var(--card-white);
    font-weight: 600;
    font-size: 34px;
    line-height: 1;
    padding: 16px 22px;
    border-radius: 10px;
  }
  .brand__mark {
    width: 92px;
    height: 92px;
    border-radius: 50%;
    background: var(--brand-blue);
  }
  .holder {
    position: absolute;
    left: 220px;
    top: 182px;
    width: 320px;
    text-align: right;
  }
  .holder__name {
    font-size: 28px;
    font-weight: 600;
    letter-spacing: 2px;
    color: var(--ink);
    margin: 0;
    line-height: 1.2;
  }
  .holder__role {
    font-size: 20px;
    color: var(--brand-blue);
    margin: 2px 0 0;
    line-height: 1.2;
  }
  .contacts {
    position: absolute;
    right: 40px;
    top: 162px;
    list-style: none;
    margin: 0;
    padding: 0;
    color: var(--card-white);
    font-size: 19px;
  }
  .contacts li {
    display: flex;
    justify-content: flex-end;
    align-items: center;
    gap: 10px;
    height: 34px;
    letter-spacing: 1px;
  }
  .contacts svg {
    width: 19px;
    height: 19px;
    fill: var(--card-white);
    flex: none;
  }
  .address {
    position: absolute;
    left: 60px;
    bottom: 46px;
    color: var(--card-white);
    font-size: 23px;
    line-height: 1.45;
    letter-spacing: 1px;
    margin: 0;
  }
</style>
</head>
<body>
  <article class="card">
    <svg class="card__waves" viewBox="0 0 980 560" aria-hidden="true">
      <defs>
        <path id="wave" d="M0,395 C190,470 400,470 560,300 C700,160 850,100 980,90 L980,620 L0,620 Z"/>
      </defs>
      <use href="#wave" transform="translate(0,-58)" fill="var(--brand-blue)"/>
      <use href="#wave" transform="translate(0,-44)" fill="var(--card-white)"/>
      <use href="#wave" transform="translate(0,-32)" fill="var(--brand-pink)"/>
      <use href="#wave" transform="translate(0,-16)" fill="var(--card-white)"/>
      <use href="#wave" fill="var(--brand-blue)"/>
    </svg>

    <div class="brand">
      <span class="brand__name">Brolvaquin Care</span>
      <span class="brand__mark" role="img" aria-label="Company emblem"></span>
    </div>

    <div class="holder">
      <p class="holder__name">MARCUS DELANEY</p>
      <p class="holder__role">Managing Director</p>
    </div>

    <ul class="contacts">
      <li>021 555 0148
        <svg viewBox="0 0 24 24"><path d="M6.6 10.8a15.1 15.1 0 0 0 6.6 6.6l2.2-2.2c.3-.3.7-.4 1-.2 1.1.4 2.3.6 3.6.6.6 0 1 .4 1 1V20c0 .6-.4 1-1 1A17 17 0 0 1 3 4c0-.6.4-1 1-1h3.5c.6 0 1 .4 1 1 0 1.3.2 2.5.6 3.6.1.3 0 .7-.2 1z"/></svg>
      </li>
      <li>021 555 0148
        <svg viewBox="0 0 24 24"><path d="M7 1h10a2 2 0 0 1 2 2v18a2 2 0 0 1-2 2H7a2 2 0 0 1-2-2V3a2 2 0 0 1 2-2zm0 3v15h10V4z"/></svg>
      </li>
      <li>021 555 0148
        <svg viewBox="0 0 24 24"><path d="M6 2h9l3 3v4h2a2 2 0 0 1 2 2v9a2 2 0 0 1-2 2H4a2 2 0 0 1-2-2v-9a2 2 0 0 1 2-2h2zm2 2v5h8V6h-2V4zm-1 9v2h2v-2zm4 0v2h2v-2zm4 0v2h2v-2zm-8 4v2h2v-2zm4 0v2h2v-2zm4 0v2h2v-2z"/></svg>
      </li>
      <li>hello@brolvaquincare.com.au
        <svg viewBox="0 0 24 24"><path d="M2 5h20v14H2zm2 2v.5l8 5.5 8-5.5V7l-8 5.2z"/></svg>
      </li>
      <li>www.brolvaquincare.com.au
        <svg viewBox="0 0 24 24"><path d="M12 2a10 10 0 1 0 0 20 10 10 0 0 0 0-20zm6.9 6h-3a15 15 0 0 0-1.3-3.9A8 8 0 0 1 18.9 8zM12 4c.8 1.2 1.5 2.5 1.9 4h-3.8c.4-1.5 1.1-2.8 1.9-4zM4.3 14a8 8 0 0 1 0-4h3.4a16 16 0 0 0 0 4zm.8 2h3a15 15 0 0 0 1.3 3.9A8 8 0 0 1 5.1 16zm3-8h-3a8 8 0 0 1 4.3-3.9A15 15 0 0 0 8.1 8zM12 20c-.8-1.2-1.5-2.5-1.9-4h3.8c-.4 1.5-1.1 2.8-1.9 4zm2.3-6H9.7a14 14 0 0 1 0-4h4.6a14 14 0 0 1 0 4zm.3 5.9a15 15 0 0 0 1.3-3.9h3a8 8 0 0 1-4.3 3.9zm1.7-5.9a16 16 0 0 0 0-4h3.4a8 8 0 0 1 0 4z"/></svg>
      </li>
    </ul>

    <p class="address">047.12th floor,Plaza<br>Harwick Road NTB</p>
  </article>
</body>
</html>
```